Business IT Services Billboard to attract local small businesses

We are Brivoqua, a premier Managed Service Provider (MSP) specializing in comprehensive IT services and VOIP phone solutions exclusively for businesses. Our goal is to create a dynamic and visually engaging billboard advertisement that not only highlights our cutting-edge IT solutions but also emphasizes our state-of-the-art VOIP phone services. This billboard should communicate our commitment to providing innovative, reliable, and holistic technology solutions.
See the attached supporting documentation.
Target Market(s)
small business
Industry/Entity Type
Information Technology
Colors
Designer to choose colors to be used in the design.
Look and feel
Each slider illustrates characteristics of the customer's brand and the style your logo design should communicate.

```html
<!DOCTYPE html>
<html lang="en">
<head>
<meta charset="UTF-8">
<title>Brivoqua Billboard</title>
<link href="https://fonts.googleapis.com/css2?family=Poppins:wght@600;700;800&display=swap" rel="stylesheet">
<style>
  :root {
    --page-bg: #c4c4c4;
    --board-bg: #f1f1f2;
    --brand-blue: #1a6fbf;
    --ink: #2a2a2b;
    --bar-dark: #2c2c2d;
    --white: #ffffff;
    --ring-tone: #dde3ea;
  }
  * { margin: 0; padding: 0; box-sizing: border-box; }
  html, body {
    width: 1038px;
    height: 1200px;
    overflow: hidden;
    background: var(--page-bg);
    font-family: "Poppins", sans-serif;
  }
  .billboard {
    position: absolute;
    left: 39px;
    top: 461px;
    width: 960px;
    height: 278px;
    background: var(--board-bg);
    box-shadow: 0 4px 6px rgba(0,0,0,0.35);
    overflow: hidden;
  }
  .tech-backdrop {
    position: absolute;
    left: 560px;
    top: -120px;
    width: 520px;
    height: 500px;
    border-radius: 50%;
    background: radial-gradient(circle, rgba(221,227,234,0) 20%, var(--ring-tone) 45%, rgba(221,227,234,0.6) 60%, rgba(241,241,242,0) 72%);
  }
  .brand-name {
    position: absolute;
    left: 33px;
    top: 70px;
    font-weight: 800;
    font-size: 31px;
    color: var(--brand-blue);
    letter-spacing: -0.5px;
  }
  .headline-lead {
    position: absolute;
    left: 205px;
    top: 26px;
    font-weight: 700;
    font-size: 25px;
    color: var(--ink);
  }
  .headline-main {
    position: absolute;
    left: 205px;
    top: 52px;
    font-weight: 800;
    font-size: 52px;
    line-height: 1;
    letter-spacing: -2px;
    color: var(--ink);
  }
  .headline-accent {
    position: absolute;
    left: 206px;
    top: 102px;
    font-weight: 800;
    font-size: 46px;
    line-height: 1;
    letter-spacing: 2px;
    color: var(--brand-blue);
  }
  .tagline-bar {
    position: absolute;
    left: 28px;
    top: 165px;
    width: 780px;
    height: 34px;
    border-radius: 6px;
    background: var(--bar-dark);
    color: var(--white);
    font-weight: 700;
    font-size: 18.5px;
    line-height: 34px;
    padding-left: 18px;
  }
  .call-to-action {
    position: absolute;
    left: 30px;
    top: 212px;
    font-weight: 700;
    font-size: 30px;
    color: var(--ink);
    letter-spacing: -0.3px;
  }
  .web-bar {
    position: absolute;
    left: 525px;
    top: 215px;
    width: 435px;
    height: 37px;
    background: var(--brand-blue);
    border-radius: 4px 0 0 4px;
    box-shadow: 0 3px 4px rgba(0,0,0,0.25);
    color: var(--white);
    font-weight: 700;
    font-size: 26px;
    line-height: 37px;
    letter-spacing: 3px;
    padding-left: 24px;
  }
  .team-photo {
    position: absolute;
    left: 782px;
    top: 40px;
    width: 178px;
    height: 178px;
    border-radius: 50%;
    border: 3px solid var(--brand-blue);
    background: linear-gradient(160deg, #5c7288 0%, #8a96a2 40%, #c9cdd2 75%, #e8e8ea 100%);
    box-shadow: 0 0 0 4px var(--board-bg);
  }
</style>
</head>
<body>
  <section class="billboard">
    <div class="tech-backdrop"></div>
    <div class="brand-name">Brivoqua</div>
    <div class="headline-lead">Elevate Your Business with</div>
    <div class="headline-main">NEXT-GEN IT AND</div>
    <div class="headline-accent">VOIP SERVICES</div>
    <div class="tagline-bar">Innovative IT and VOIP Solutions Tailored for Your Business Success</div>
    <div class="call-to-action">Transform Your Tech Today!</div>
    <div class="web-bar">www.brivoqua.com</div>
    <div class="team-photo" role="img" aria-label="Photo of a support agent on a headset phone at a desk in a modern office"></div>
  </section>
</body>
</html>
```